Backdrop Banner to be designed for a kids handwriting company

We are an occupational therapy company that helps children improve their handwriting. We give online lessons and make how-to videos for the kids to watch. We are looking for a backdrop to be designed that can be placed on a roller blind to use when needed. Size to be 183cm (width) x200cm (height). The final design needs to be produced in a format that can be uploaded to a printing company for them to produce.

We need our logo to be displayed. Our corporate colours are: #ff0069, #2abeb0, #ffc700, #93db40, #322e58. If you wish to see our current 'look' go to www.penpathlearning.co.uk. We can tell you our fonts if asked.

We work with children aged 6 to 16 years, mainly 10 to 13 years. In the past, I have placed motivational stickers on the back of my wall. Many of the children we see have lost confidence in themselves hence the words 'Believe in yourself', 'Make it happen' etc. were chosen. We teach them how to write clearly so the teachers can read/mark their work, parents are happy and we boost their self confidence. We are open to positive words or doodle style images but they cannot be cutesy. The backdrop must not overpower a lesson and take away the kid's focus.

I have included some ideas, our logo and a picture of what is the backdrop in my office.
1. We are open to keeping everything in the right-hand corner of the screen so the kids see us and any image is to the right (as per the picture). If doing this the images will need to sit from 30cm to 80cm from the top of the blind when fully down. Width needed is probably 65cm.
2. We are open to the parkour concept of words and images going across the whole backdrop or on the right hand side.
3. We are open to the backdrop having one image on its own whether that be random or specific images.
4. If using any writing the font has to be readable, no imitation of 'bad' handwriting. We see kids at any time of the day so we cannot have it say 'Good morning'.

We are hoping you will be inspired by this project as we'd love to work with you and see your ideas.

UPDATE 1 - 03.08.23: Based on the designs submitted so far please watch the wording of any motivational words and keep in mind this is a backdrop banner only the top half is likely to be seen on screen and there will be a person sitting in front of your design.

UPDATE 2 - 04.08.23: Mock up images with measurements added to help you design this backdrop for a video.

UPDATE: Based on the designs submitted so far please watch the wording of any motivational words and keep in mind this is a backdrop banner only the top half is likely to be seen on screen and there will be a person sitting in front of your design.

Supplied this in the brief

Other font styles liked:
• Business fonts on website are Kind Heart, Logo is Typo Round Regular

• Supplied this in the brief

```html
<!DOCTYPE html>
<html lang="en">
<head>
<meta charset="utf-8">
<title>Believe in yourself – Backdrop Banner</title>
<link rel="stylesheet" href="https://fonts.googleapis.com/css2?family=Mali:wght@500&display=swap">
<style>
  :root {
    --navy: #221c6b;
    --indigo: #23307a;
    --teal: #2abeb0;
    --lime: #a8d832;
    --orange: #f2762e;
    --magenta: #c8226b;
    --violet: #5a2a7a;
    --white: #ffffff;
    --child-tone: #4a3a52;
  }
  * { margin: 0; padding: 0; box-sizing: border-box; }
  html, body {
    width: 959px;
    height: 1200px;
    overflow: hidden;
    background: #ffffff;
  }
  .banner {
    position: relative;
    width: 959px;
    height: 1200px;
    overflow: hidden;
    background: linear-gradient(180deg, var(--navy) 0%, var(--navy) 42%, var(--indigo) 60%, #247a93 80%, var(--teal) 100%);
  }
  .starburst {
    position: absolute;
    left: 0;
    top: 0;
    width: 959px;
    height: 1200px;
  }
  .child-illustration {
    position: absolute;
    left: 640px;
    top: 310px;
    width: 200px;
    height: 250px;
  }
  .motto {
    position: absolute;
    left: 600px;
    top: 232px;
    width: 300px;
    font-family: "Mali", cursive;
    font-weight: 500;
    font-size: 38px;
    line-height: 1;
    color: var(--white);
    white-space: nowrap;
  }
  .brand-name {
    position: absolute;
    left: 764px;
    top: 574px;
    font-family: "Mali", cursive;
    font-weight: 500;
    font-size: 19px;
    line-height: 1;
    color: var(--white);
    white-space: nowrap;
  }
</style>
</head>
<body>
  <main class="banner">
    <svg class="starburst" viewBox="0 0 959 1200" role="img" aria-label="Rainbow starburst of sharp rays radiating from a bright lime-green star">
      <defs>
        <radialGradient id="burst-glow" cx="640" cy="420" r="520" gradientUnits="userSpaceOnUse">
          <stop offset="0" stop-color="var(--lime)"/>
          <stop offset="0.2" stop-color="#7fc64a"/>
          <stop offset="0.36" stop-color="var(--orange)" stop-opacity="0.85"/>
          <stop offset="0.55" stop-color="var(--magenta)" stop-opacity="0.55"/>
          <stop offset="0.78" stop-color="var(--violet)" stop-opacity="0.3"/>
          <stop offset="1" stop-color="var(--violet)" stop-opacity="0"/>
        </radialGradient>
      </defs>
      <ellipse cx="640" cy="440" rx="620" ry="560" fill="url(#burst-glow)"/>
    </svg>

    <p class="motto">Believe in yourself</p>

    <svg class="child-illustration" viewBox="0 0 200 250" role="img" aria-label="Drawing of a girl seen from behind in a striped top, writing colourful letters in the air">
      <defs>
        <linearGradient id="child-fill" x1="0" y1="0" x2="0" y2="1">
          <stop offset="0" stop-color="#6b4a3a"/>
          <stop offset="1" stop-color="var(--child-tone)"/>
        </linearGradient>
      </defs>
      <rect width="200" height="250" rx="14" fill="url(#child-fill)" opacity="0.85"/>
    </svg>

    <p class="brand-name">PenPath Learning</p>
  </main>
</body>
</html>
```